Flyer für ambulanten Pflegedienst
Zielgruppe
Ambulanter Pflegedienst in Gründung. Habe schon ein Logo und Text. Zielgruppe sind Pflege und Hilfsbedürftige Menschen

```html
<!DOCTYPE html>
<html lang="de">
<head>
<meta charset="utf-8">
<title>Auenhaus – Broschüre</title>
<link href="https://fonts.googleapis.com/css2?family=Alike&family=Open+Sans:wght@400;600;700&display=swap" rel="stylesheet">
<style>
  :root{
    --teal:#5db7ad;
    --teal-soft:#8fd0c7;
    --blue:#3f8fb8;
    --ink:#2a2a2a;
    --paper:#ffffff;
    --backdrop:#eeeeef;
    --photo-a:#b9d5dc;
    --photo-b:#7fa9b6;
  }
  *{box-sizing:border-box;margin:0;padding:0}
  html,body{width:1200px;height:625px;overflow:hidden;background:var(--backdrop)}
  body{position:relative;font-family:"Open Sans",sans-serif;color:var(--ink)}
  .page{position:absolute;top:42px;height:540px;background:var(--paper);overflow:hidden;box-shadow:0 4px 14px rgba(0,0,0,.12)}
  .cover{left:36px;width:350px}
  .spread-left{left:440px;width:362px}
  .spread-right{left:802px;width:362px}
  .abs{position:absolute}
  .band{position:absolute;left:0;right:0;bottom:0;height:29px;background:linear-gradient(90deg,var(--teal),var(--blue));color:#fff;font-size:8.6px;font-weight:600;letter-spacing:.5px;display:flex;align-items:center}

  /* cover */
  .brand{left:66px;top:62px;display:flex;align-items:center;gap:12px}
  .brand-dot{width:26px;height:26px;border-radius:50%;background:var(--teal)}
  .brand-name{font-family:"Alike",serif;font-size:34px;color:var(--teal);line-height:1;letter-spacing:.5px}
  .service-list{list-style:none;font-family:"Alike",serif;color:var(--blue);font-size:10.4px;line-height:1.15}
  .service-list li{margin-bottom:5.5px}
  .service-list small{display:block;font-size:7.4px}
  .cover-photo{left:112px;top:262px;right:0;bottom:29px;border-top-left-radius:240px 250px;background:linear-gradient(160deg,var(--photo-a),var(--photo-b))}
  .leaf-patch{border-radius:50%;background:radial-gradient(circle,var(--teal-soft),rgba(143,208,199,0) 70%)}
  .claim-circle{left:9px;top:322px;width:154px;height:154px;border-radius:50%;background:var(--teal);color:#fff;font-family:"Alike",serif;font-size:10.6px;line-height:1.5;text-align:center;display:flex;align-items:center;justify-content:center;padding:10px}

  /* left inner page */
  .section-title{font-family:"Alike",serif;color:var(--blue);font-size:12.4px;letter-spacing:.3px}
  .copy{font-size:7.8px;line-height:1.6}
  .inner-photo{left:0;top:278px;width:276px;bottom:29px;border-top-right-radius:220px 240px;background:linear-gradient(150deg,#e3e6e4,#c4cfd3 60%,#aeb9c4)}
  .services-circle{left:166px;top:160px;width:172px;height:172px;border-radius:50%;background:var(--teal);color:#fff;font-weight:600;font-size:8.4px;line-height:1.6;text-align:center;display:flex;align-items:center;justify-content:center;padding:12px}

  /* right inner page */
  .col-title{font-family:"Alike",serif;color:var(--blue);font-size:12.4px;line-height:1.2;letter-spacing:.3px}
  .col-intro{color:var(--blue);font-weight:700;font-size:7.3px;line-height:1.75}
  .task-list{list-style:none;font-size:7.9px;line-height:1.64}
  .task-list small{font-size:5.5px}
  .task-list .fine{display:block;font-size:5.4px;line-height:1.5}
</style>
</head>
<body>

<section class="page cover">
  <div class="abs brand"><span class="brand-dot"></span><span class="brand-name">Auenhaus</span></div>

  <ul class="abs service-list" style="left:66px;top:142px">
    <li>Grundpflege</li>
    <li>Behandlungspflege</li>
    <li>24-Stunden Pflege</li>
    <li>Hauswirtschaftlicher<br>Versorgung</li>
  </ul>
  <ul class="abs service-list" style="left:203px;top:143px">
    <li>Betreuungs- und<br>Entlastungsleistungen<small>nach § 45 SGB XI</small></li>
    <li>Verhinderungspflege</li>
    <li>Alltagsbegleitung</li>
    <li>Palliativ Pflege</li>
  </ul>

  <div class="abs cover-photo" role="img" aria-label="Foto: Hände halten ein Papierherz mit einem Seniorenpaar"></div>
  <div class="abs leaf-patch" style="left:6px;top:240px;width:130px;height:100px" role="img" aria-label="Dekoration: türkise Blätter"></div>
  <div class="abs claim-circle">Wir stehen<br>für hochwertige<br>&amp; individuelle<br>Unterstützungen<br>mit Herz - für ein<br>selbstbestimmtest<br>Leben zu<br>Hause</div>

  <div class="band" style="justify-content:flex-end;padding-right:20px">Wir nehmen uns die Zeit zur Sicherung Ihrer Lebensqualität</div>
</section>

<section class="page spread-left">
  <h2 class="abs section-title" style="left:24px;top:24px">Wir sind für Sie da</h2>
  <p class="abs copy" style="left:24px;top:48px;width:318px">Uns liegt es am Herzen durch qualitativ hochwertige und individuelle Unterstützungen den Menschen ein selbstbestimmtest Leben zu ermöglichen. Wir setzten auf Fachkompetenz und Empathie, um sicherzustellen, dass unsere Kunden die bestmögliche medizinische Versorgung erhalten.</p>
  <p class="abs copy" style="left:24px;top:110px;width:196px">Unsere Dienstleistung umfasst die ambulante Pflege gemäß SGB CI sowie die Behandlungspflege gemäß SGB V. Betreuungs- und Entlastungszeiten nach § 45 SGB XI um Menschen im Alltag zu unterstützen und ihre Lebensqualität zu steigern.</p>
  <p class="abs copy" style="left:24px;top:188px;width:150px">Pflegebedürftig ist, wer aufgrund einer körperlichen, geistigen oder seelischen Krankheit bzw. Behinderung in erheblichen Umfang Hilfe bis hin zur vollumfänglichen Betreuung benötigt.</p>

  <div class="abs inner-photo" role="img" aria-label="Foto: Pflegerin misst einer lächelnden Seniorin im Bett den Blutdruck"></div>
  <div class="abs leaf-patch" style="left:230px;top:95px;width:120px;height:90px" role="img" aria-label="Dekoration: türkise Blätter"></div>
  <div class="abs leaf-patch" style="left:262px;top:330px;width:90px;height:80px" role="img" aria-label="Dekoration: türkise Blätter"></div>
  <div class="abs services-circle">Die Leistung des Altenpflege- und Seniorenbetreuungsdienstes erstrecken sich auf die Grundpfleg, Behandlungspflege, 24-Stundenpflege, ambulante Palliative Pflege, hauswirtschaftliche Versorgung, Verhinderungspflege und Alltagsbegleitung.</div>

  <div class="band" style="padding-left:24px">Für ein selbstbestimmtes Leben in den eigenen vier Wänden</div>
</section>

<section class="page spread-right">
  <h3 class="abs col-title" style="left:24px;top:24px">Grundpflege</h3>
  <p class="abs col-intro" style="left:24px;top:44px;width:140px">In der Grundpflege werden die Pflegepersonen in der Verrichtung alltäglicher Grundverrichtungen unterstützt, z.B.</p>
  <ul class="abs task-list" style="left:24px;top:104px">
    <li>Dusche</li><li>Baden</li><li>Zahnpflege</li><li>Rasieren</li><li>Kämmen</li><li>An- und Auskleiden</li><li>Hilfsmittelversorgung</li><li>Mobilisation</li><li>Prophylaxen</li><li>Nahrungsaufnahme</li><li>Toilettengang usw.</li>
  </ul>

  <h3 class="abs col-title" style="left:24px;top:268px">Behandlungspflege</h3>
  <p class="abs col-intro" style="left:24px;top:287px;width:144px">Die Behandlungspflege umfasst alle Pflegedienste, die auf ärztlicher Verordnung hin vom Pflegepersonal durchgeführt werden, z.B.</p>
  <ul class="abs task-list" style="left:24px;top:340px">
    <li>Pulsmessung</li><li>Blutdruckmessung</li><li>Blutzuckermessung</li><li>Wundversorgung</li><li>Verbandswechsel</li><li>Injektionen <small>(z.B. Insulin)</small></li><li>Stellen der Medikamente</li><li>Anlegen von Kompressionsverbänden</li><li>An- und Ausziehen von<br>Kompressionsstrümpfen usw.</li>
  </ul>

  <h3 class="abs col-title" style="left:180px;top:26px">24-Stunden Pflege</h3>
  <p class="abs col-intro" style="left:180px;top:46px;width:150px">In verschiedenen Situationen ist die stundenweise Pflege nicht ausreichend, z.B. in der Folgezeit eines Krankenhausaufenthaltes. Es wird eine 24-Stunden-Pflege angeboten, im Rahmen derer das Pflegepersonal rund um die Uhr erreichbar ist. Typische Leistungen sind:</p>
  <ul class="abs task-list" style="left:180px;top:152px">
    <li>Überwachung der Vitalsituation<br>des Patienten</li><li>Verabreichung von Medikamenten</li><li>Wundversorgung</li><li>Verbandswechsel</li><li>Katheter Versorgung usw.</li>
  </ul>

  <h3 class="abs col-title" style="left:180px;top:256px">Hauswirtschaftlicher<br>Versorgung</h3>
  <p class="abs col-intro" style="left:180px;top:292px;width:150px">In der hauswirtschaftlichen Versorgung werden sämtliche hauswirtschaftlichen Tätigkeiten übernommen, z.B.</p>
  <ul class="abs task-list" style="left:180px;top:340px">
    <li>Einkaufen</li><li>Besorgungen</li><li>Zubereitung von Mahlzeiten</li><li>Abwaschen</li><li>Wäsche waschen</li><li>Bügeln</li><li>Reinigungsarbeiten<span class="fine">(Aufräumen, Toilette, Bad, Küche, Wohn- und Schlafbereich, Staubsaugen, Staubwischen)</span></li><li>Betreuung von Haustieren</li><li>Heizen der Wohnung <small>(Holz, Kohle, Öl)</small></li><li>Fahrdienste</li>
  </ul>

  <div class="band" style="justify-content:flex-end;padding-right:24px">Mit uns meistern Sie Ihren Alltag</div>
</section>

</body>
</html>
```